4th Generation Family Business Needs a New Card Design!

We are a family owned 4th Generation company. We are based in the Sydney, Australia area and we are desperately in need of a more modern and classy card. We are monumental masons who design, supply & erect lasting memorials throughout cemeteries in Sydney. Our customers are normally in a period of grieving. I have attached logo files that will need to be implemented on the card. Company was established 1935. Australian Owned and Operated. Card needs to be designed to PIXO.com specification.

Target Market(s)

Our target market is based upon people that a grieving for family members that have passed away. We also deal with alot of companies that own and operate cemeteries.

Industry/Entity Type

Business

Contact Information for Business Card

Simon Harcourt, Operations Manager, 0417293086, simon@harcourtmemorials.com.au
Lewis Harcourt, Director, 0491630572, lewis@harcourtmemorials.com.au
Phone # 02 9561 3048
Website: www.harcourtmemorials.com.au
Address: Suite 17, 8 Palfrey Lane, West Carlow, Sydney NSW 2156

Font styles to use
Serif
Decorative
Script

Requirements
Must have
• Would like to see the logo nicely implemented with a modern design. Embossed lettering would be a nice additive.

```html
<!DOCTYPE html>
<html lang="en">
<head>
<meta charset="utf-8">
<title>Harcourt Memorials – Business Card</title>
<link href="https://fonts.googleapis.com/css2?family=Open+Sans:ital,wght@0,600;1,400;1,700&display=swap" rel="stylesheet">
<style>
  :root {
    --backdrop: #3a3a3c;
    --granite-light: #7a807f;
    --granite-mid: #646a69;
    --granite-dark: #4f5453;
    --gold: #f2b705;
    --ink: #ffffff;
  }
  * { margin: 0; padding: 0; box-sizing: border-box; }
  html, body { width: 1200px; height: 675px; overflow: hidden; }
  body {
    background: var(--backdrop);
    font-family: "Open Sans", Arial, sans-serif;
    color: var(--ink);
    position: relative;
  }
  .card {
    position: absolute;
    top: 178px;
    width: 540px;
    height: 320px;
    border-radius: 3px;
    background:
      radial-gradient(circle at 30% 25%, var(--granite-light) 0%, transparent 60%),
      radial-gradient(circle at 75% 80%, var(--granite-dark) 0%, transparent 65%),
      var(--granite-mid);
    box-shadow: 0 14px 30px rgba(0,0,0,.45);
  }
  .card--contact { left: 40px; }
  .card--brand { left: 620px; }

  .contact { position: absolute; left: 44px; top: 34px; font-style: italic; font-size: 13px; line-height: 1.45; }
  .contact__name { color: var(--gold); font-weight: 700; font-size: 19px; letter-spacing: .3px; text-transform: uppercase; margin-left: 10px; }
  .contact__role, .contact__email { margin-left: 8px; }
  .rule { width: 26px; height: 1.5px; background: var(--gold); margin: 12px 0 12px 4px; }
  .label { color: var(--gold); font-weight: 700; }
  .contact__address { margin-left: -6px; }

  .brand {
    position: absolute; inset: 0;
    display: flex; align-items: center; justify-content: center;
    padding-top: 40px;
  }
  .brand__name {
    font-weight: 600;
    font-size: 30px;
    letter-spacing: 2px;
    text-transform: uppercase;
    color: var(--ink);
    text-align: center;
    line-height: 1.15;
  }
</style>
</head>
<body>
  <section class="card card--contact" aria-label="Contact side">
    <div class="contact">
      <p class="contact__name">Simon Harcourt</p>
      <p class="contact__role">Operations Manager</p>
      <p class="contact__email">simon@harcourtmemorials.com.au</p>
      <div class="rule"></div>
      <p><span class="label">Cell:</span> 0417293086</p>
      <p><span class="label">Phone:</span> 02 9561 3048</p>
      <p>harcourtmemorials.com.au</p>
      <div class="rule"></div>
      <p class="contact__address">Suite 17, 8 Palfrey Lane<br>West Carlow<br>Sydney NSW 2156</p>
    </div>
  </section>

  <section class="card card--brand" aria-label="Brand side">
    <div class="brand">
      <p class="brand__name">Harcourt<br>Memorials</p>
    </div>
  </section>
</body>
</html>
```